Corvane Capital Business Cards

These are professional business cards that are for my family office.
Put fake emails and phone numbers as of now until I finalize those components. This family office controls my families investments, assets, and future. The cards should be professional.
..
.
.
.
I just uploaded another variation of a logo I would like to see as a business card to I am inbeteen which logo to use

Target Market(s)

business

Industry/Entity Type

business

Contact Information for Business Card

Professional, wealth related, finance related.

Requirements
Must have
• Logo

```html
<!DOCTYPE html>
<html lang="en">
<head>
<meta charset="utf-8">
<title>Corvane Capital Business Cards</title>
<link rel="stylesheet" href="https://fonts.googleapis.com/css2?family=Bodoni+Moda:wght@400&family=Tinos:wght@400;700&display=swap">
<style>
  :root {
    --backdrop: #a88c70;
    --card-black: #000000;
    --card-gold: #c5ae6f;
    --gold: #d4bd7c;
    --white: #ffffff;
    --ink: #111111;
  }
  * { margin: 0; padding: 0; box-sizing: border-box; }
  html, body { width: 1200px; height: 749px; overflow: hidden; }
  body {
    position: relative;
    background: var(--backdrop);
    font-family: "Tinos", "Times New Roman", serif;
  }
  .card {
    position: absolute;
    top: 226px;
    width: 502px;
    height: 286px;
    overflow: hidden;
    box-shadow: 0 4px 10px rgba(0, 0, 0, 0.35);
  }
  .card--front { left: 98px; background: var(--card-black); color: var(--white); }
  .card--back { left: 608px; background: var(--card-gold); }

  .mark-area { position: absolute; top: 0; height: 100%; }
  .card--front .mark-area {
    left: 250px; right: 0;
    background: linear-gradient(90deg, var(--card-black) 0%, #3a3a3a 35%, var(--white) 70%, var(--card-gold) 100%);
  }
  .card--back .mark-area {
    left: 0; width: 255px;
    background: linear-gradient(90deg, var(--white) 0%, var(--card-gold) 45%, var(--white) 80%, var(--card-gold) 100%);
  }

  .wordmark {
    position: absolute;
    font-family: "Bodoni Moda", "Times New Roman", serif;
    font-weight: 400;
    letter-spacing: 0.3px;
    white-space: nowrap;
  }
  .card--front .wordmark { left: 18px; top: 35px; font-size: 18px; color: var(--white); }
  .card--back .wordmark { right: 19px; top: 234px; font-size: 21px; color: var(--ink); }

  .holder-name {
    position: absolute; left: 18px; top: 153px;
    font-size: 17px; font-weight: 700; letter-spacing: 0.3px; line-height: 20px;
  }
  .holder-name .surname { color: var(--gold); }
  .holder-role { position: absolute; left: 18px; top: 176px; font-size: 14px; line-height: 18px; }
  .divider {
    position: absolute; left: 18px; top: 202px;
    width: 17px; height: 4px; background: var(--gold);
  }
  .contact {
    position: absolute; left: 18px; top: 226px;
    list-style: none; font-size: 14px; line-height: 21px;
  }
  .contact li { display: flex; align-items: center; gap: 5px; }
  .contact svg { width: 14px; height: 11px; fill: var(--gold); }
</style>
</head>
<body>
  <section class="card card--front" aria-label="Business card front">
    <div class="mark-area" role="img" aria-label="Large brand mark decoration"></div>
    <div class="wordmark">CORVANE CAPITAL</div>
    <div class="holder-name">Elliot <span class="surname">Harrow</span></div>
    <div class="holder-role">Founder</div>
    <div class="divider"></div>
    <ul class="contact">
      <li>
        <svg viewBox="0 0 14 11" aria-hidden="true"><path d="M1 3 C1 1 13 1 13 3 L13 4 L10 4 L10 3 L4 3 L4 4 L1 4 Z M3 5 L11 5 L13 10 L1 10 Z"/></svg>
        <span>555-214-7390</span>
      </li>
      <li>
        <svg viewBox="0 0 14 11" aria-hidden="true"><path d="M0 1 L14 1 L7 6 Z M0 2.5 L7 7.5 L14 2.5 L14 10 L0 10 Z"/></svg>
        <span>office@corvanemail.com</span>
      </li>
    </ul>
  </section>

  <section class="card card--back" aria-label="Business card back">
    <div class="mark-area" role="img" aria-label="Large brand mark decoration"></div>
    <div class="wordmark">CORVANE CAPITAL</div>
  </section>
</body>
</html>
```